BOLD & MINIMALIST DESIGN NEEDED

We want a very bold but minimalistic business card design that is impactful and utilizes both sides of the business card. Our current logo is included for your use.

We want bold fonts and good use of negative space. We don't want the logo to overpower the design.

Target Market(s)

Professionals who are building new commercial buildings.

Industry/Entity Type

Construction

Contact Information for Business Card

Name, Title, email, office phone, cell phone, website

Font styles to use
Serif
Sans Serif

Requirements
Must have
• Bold design!

```html
<!DOCTYPE html>
<html lang="en">
<head>
<meta charset="utf-8">
<title>Ridgecrest – Business Card</title>
<link rel="stylesheet" href="https://fonts.googleapis.com/css2?family=Montserrat:wght@500;600;800;900&display=swap">
<style>
  :root {
    --bg-dark: #2f2f2f;
    --bg-light: #5c5c5c;
    --card-white: #f4f4f2;
    --card-black: #141414;
    --ink: #0d0d0d;
    --accent-green: #5fae24;
    --accent-green-dark: #4a8f1a;
  }
  * { margin: 0; padding: 0; box-sizing: border-box; }
  html, body {
    width: 1200px;
    height: 1050px;
    overflow: hidden;
  }
  body {
    background: linear-gradient(135deg, var(--bg-dark) 0%, var(--bg-light) 100%);
    font-family: "Montserrat", sans-serif;
    color: var(--ink);
    position: relative;
  }
  .card {
    position: absolute;
    width: 540px;
    height: 315px;
    border-bottom: 6px solid var(--accent-green);
    box-shadow: 0 24px 40px rgba(0,0,0,0.35);
  }
  /* Front side */
  .card-front {
    left: 90px;
    top: 600px;
    background: var(--card-white);
  }
  .front-brand {
    position: absolute;
    left: 38px;
    top: 50%;
    transform: translate(-50%, -50%) rotate(-90deg) translateY(50%);
    transform-origin: center;
    font-weight: 900;
    font-size: 40px;
    letter-spacing: 0.5px;
    white-space: nowrap;
    color: var(--ink);
  }
  .front-brand-wrap {
    position: absolute;
    left: 30px;
    top: 0;
    bottom: 0;
    width: 60px;
  }
  .front-brand-wrap .front-brand {
    left: 30px;
    transform: translate(-50%, -50%) rotate(-90deg);
  }
  .person {
    position: absolute;
    left: 300px;
    top: 58px;
  }
  .person-name {
    font-weight: 900;
    font-size: 34px;
    line-height: 0.95;
    text-transform: uppercase;
  }
  .person-title {
    font-weight: 600;
    font-size: 13px;
    margin-top: 6px;
  }
  .contact {
    position: absolute;
    left: 300px;
    top: 170px;
    font-weight: 600;
    font-size: 12.5px;
    line-height: 1.5;
  }
  .contact-address { margin-bottom: 8px; }
  .contact-line {
    display: flex;
    align-items: center;
    gap: 6px;
  }
  .contact-icon { width: 11px; height: 11px; flex: none; }
  /* Back side */
  .card-back {
    left: 590px;
    top: 190px;
    background: var(--card-black);
    display: flex;
    align-items: center;
    justify-content: center;
    gap: 14px;
  }
  .back-mark {
    width: 22px;
    height: 22px;
    background: var(--accent-green);
  }
  .back-brand {
    font-weight: 900;
    font-size: 46px;
    letter-spacing: 1px;
    color: #050505;
    text-shadow: none;
  }
</style>
</head>
<body>
  <section class="card card-front" aria-label="Business card front">
    <div class="front-brand-wrap">
      <div class="front-brand">RIDGECREST</div>
    </div>

    <div class="person">
      <div class="person-name">Mara<br>Keller</div>
      <div class="person-title">Director</div>
    </div>

    <div class="contact">
      <div class="contact-address">Lindenweg 14,<br>30159 Hannover</div>
      <div class="contact-line">
        <svg class="contact-icon" viewBox="0 0 24 24" aria-hidden="true"><path fill="currentColor" d="M6.6 10.8a15.1 15.1 0 0 0 6.6 6.6l2.2-2.2a1 1 0 0 1 1-.25 11.4 11.4 0 0 0 3.6.57 1 1 0 0 1 1 1V20a1 1 0 0 1-1 1A17 17 0 0 1 3 4a1 1 0 0 1 1-1h3.5a1 1 0 0 1 1 1c0 1.25.2 2.45.57 3.57a1 1 0 0 1-.25 1z"/></svg>
        <span>0160 5550142</span>
      </div>
      <div class="contact-line">
        <svg class="contact-icon" viewBox="0 0 24 24" aria-hidden="true"><rect x="2" y="5" width="20" height="14" fill="none" stroke="currentColor" stroke-width="2.4"/><path d="M2 5l10 8 10-8" fill="none" stroke="currentColor" stroke-width="2.4"/></svg>
        <span>info@ridgecrest-build.com</span>
      </div>
      <div class="contact-line">
        <svg class="contact-icon" viewBox="0 0 24 24" aria-hidden="true"><circle cx="12" cy="12" r="10" fill="none" stroke="currentColor" stroke-width="2"/><ellipse cx="12" cy="12" rx="4.5" ry="10" fill="none" stroke="currentColor" stroke-width="2"/><path d="M2 12h20M4 7h16M4 17h16" stroke="currentColor" stroke-width="1.6"/></svg>
        <span>www.ridgecrest-build.com</span>
      </div>
    </div>
  </section>

  <section class="card card-back" aria-label="Business card back">
    <div class="back-mark" aria-hidden="true"></div>
    <div class="back-brand">RIDGECREST</div>
  </section>
</body>
</html>
```